Stonereach Capital Partners
Business Cards
Stonereach Capital Partners - Financial Services
Creative Brief
Simple
Daniel Morrow
Managing Director
4352 Harlow Court Suite 200 Atlanta, GA 30417
Use 214-555-0187 Will supply updated number
dmorrow@stonereachcapital.example
www.stonereachcapital.example
The will be business cards for Daniel Morrow (Managing Director) and Philip Vantanne (Managing Director). Address and phone numbers may change slightly this week. We are not sure if putting cell phones on yet. I once had a very simple business card in a basic font on high quality paper that looked great. Want very simple and professional. The logo can be on the front or keep the front simple and put the logo on the back.
Stonereach LOGO attached (unless your design has it on the front)

```html
<!DOCTYPE html>
<html lang="en">
<head>
<meta charset="utf-8">
<title>Stonereach Capital Partners – Business Cards</title>
<link rel="stylesheet" href="https://fonts.googleapis.com/css2?family=Open+Sans:wght@400;600;700&display=swap">
<style>
  :root {
    --backdrop: #e9ecef;
    --card-white: #ffffff;
    --brand-blue: #1b72b8;
    --brand-deep: #0c4f8e;
    --brand-sky: #4aa3e0;
    --accent-green: #7cc242;
    --ink-grey: #5d6670;
    --band-light: #d7e9f6;
  }
  * { margin: 0; padding: 0; box-sizing: border-box; }
  html, body { width: 1200px; height: 901px; overflow: hidden; }
  body {
    background: var(--backdrop);
    font-family: "Open Sans", Arial, sans-serif;
    position: relative;
  }
  .card {
    position: absolute;
    width: 560px;
    height: 320px;
    border-radius: 16px;
    overflow: hidden;
    box-shadow: 0 10px 28px rgba(0,0,0,0.18);
  }
  /* Front */
  .card-front { left: 60px; top: 140px; background: var(--card-white); }
  .brand-lockup {
    position: absolute; left: 34px; top: 92px; width: 230px;
    display: flex; flex-direction: column; align-items: center;
  }
  .brand-dot {
    width: 46px; height: 46px; border-radius: 50%;
    background: var(--brand-blue); margin-bottom: 10px;
  }
  .brand-name {
    color: var(--brand-blue); font-weight: 700;
    font-size: 30px; line-height: 1.05; text-align: center;
  }
  .brand-name .brand-sub { display: block; font-size: 12.5px; letter-spacing: 3.2px; margin-top: 4px; }
  .contact { position: absolute; left: 300px; top: 52px; color: var(--ink-grey); }
  .contact-name { color: var(--brand-blue); font-weight: 600; font-size: 25px; line-height: 1.1; }
  .contact-title { font-size: 11.5px; margin-bottom: 22px; }
  .contact-line { font-size: 11.5px; line-height: 1.5; display: flex; align-items: center; gap: 6px; }
  .contact-line svg { width: 11px; height: 11px; flex: none; }
  .contact-address { margin-bottom: 8px; }
  .band { position: absolute; left: 0; right: 0; }
  .band-green { top: 238px; height: 3px; background: var(--accent-green); }
  .band-blue {
    top: 241px; height: 30px;
    background: linear-gradient(90deg, var(--brand-deep), var(--brand-blue) 60%, var(--brand-sky));
    color: #fff; font-size: 13px; text-align: right; padding-right: 26px; line-height: 30px;
  }
  .band-light { top: 271px; height: 8px; background: var(--band-light); }
  /* Back */
  .card-back {
    left: 620px; top: 470px;
    background: linear-gradient(160deg, var(--brand-sky) 0%, var(--brand-blue) 45%, var(--brand-deep) 100%);
  }
  .back-glow {
    position: absolute; left: 40px; top: 20px; width: 260px; height: 260px; border-radius: 50%;
    background: radial-gradient(circle, rgba(255,255,255,0.35), rgba(255,255,255,0) 70%);
  }
  .back-brand {
    position: absolute; right: 34px; top: 128px;
    color: #fff; font-weight: 700; font-size: 32px; line-height: 1.05; text-align: center;
  }
  .back-brand .brand-sub { display: block; font-size: 12.5px; letter-spacing: 3.4px; margin-top: 4px; }
</style>
</head>
<body>
  <section class="card card-front" aria-label="Business card front">
    <div class="brand-lockup">
      <span class="brand-dot"></span>
      <p class="brand-name">Stonereach<span class="brand-sub">CAPITAL PARTNERS</span></p>
    </div>
    <div class="contact">
      <h1 class="contact-name">Daniel Morrow</h1>
      <p class="contact-title">Managing Director</p>
      <div class="contact-address">
        <p class="contact-line">4352 Harlow Court</p>
        <p class="contact-line">Suite 200</p>
        <p class="contact-line">Atlanta, GA 30417</p>
      </div>
      <p class="contact-line">
        <svg viewBox="0 0 12 12" aria-hidden="true"><path d="M3 1h2l1 3-1.5 1a6 6 0 0 0 2.5 2.5L8 6l3 1v2a2 2 0 0 1-2 2A8 8 0 0 1 1 3a2 2 0 0 1 2-2z" fill="var(--accent-green)"/></svg>
        214-555-0187
      </p>
      <p class="contact-line">
        <svg viewBox="0 0 12 12" aria-hidden="true"><rect x="0.5" y="2" width="11" height="8" rx="1" fill="var(--accent-green)"/><path d="M1 2.5l5 4 5-4" stroke="#fff" fill="none"/></svg>
        dmorrow@stonereachcapital.example
      </p>
    </div>
    <div class="band band-green"></div>
    <div class="band band-blue">www.stonereachcapital.example</div>
    <div class="band band-light"></div>
  </section>

  <section class="card card-back" aria-label="Business card back">
    <div class="back-glow" role="img" aria-label="Soft light glow decoration"></div>
    <p class="back-brand">Stonereach<span class="brand-sub">CAPITAL PARTNERS</span></p>
  </section>
</body>
</html>
```